Nivel Crest - Powerpoint Templates

We are a consultancy to help builders to optimize their planning in order to save building costs. For that reason we need templates for teasers and presentations where we offer our services, show our team and their capacities and present workflows, organization charts, price lists etc.

```html
<!DOCTYPE html>
<html lang="en">
<head>
<meta charset="utf-8">
<title>Nivel Crest – Presentation Template Overview</title>
<link href="https://fonts.googleapis.com/css2?family=Poppins:ital,wght@0,400;0,500;0,600;0,700;1,400&display=swap" rel="stylesheet">
<style>
:root{
  --canvas:#f4ece4;
  --paper:#ffffff;
  --ink:#1d1d1d;
  --muted:#8a8a8a;
  --gold:#c48f3f;
  --gold-lt:#e6c06a;
  --gold-dk:#9c6a28;
  --gold-grad:linear-gradient(135deg,#a56f2a 0%,#dcb25a 50%,#b27b33 100%);
  --night:#0d0d0d;
  --navy:#3d4863;
  --pale:#f0d488;
  --line:#e6e1db;
}
*{box-sizing:border-box;margin:0;padding:0}
html,body{width:1200px;height:696px;overflow:hidden;background:var(--canvas);font-family:"Poppins",sans-serif;color:var(--ink)}
.board{position:absolute;left:0;top:0;width:2520px;height:1461px;transform:scale(0.47619);transform-origin:0 0}
.slide{position:absolute;width:386px;height:214px;background:var(--paper);overflow:hidden}
.slide.dark{background:var(--night);color:#fff}
.c1{left:70px}.c2{left:469px}.c3{left:868px}.c4{left:1267px}.c5{left:1666px}.c6{left:2065px}
.r1{top:58px}.r2{top:284px}.r3{top:510px}.r4{top:736px}.r5{top:962px}.r6{top:1188px}
.abs{position:absolute}
.ttl{position:absolute;left:0;right:0;text-align:center;font-size:12.5px;font-weight:700;line-height:1}
.ttl.left{text-align:left;right:auto}
.ttl em{font-style:normal;color:var(--gold)}
.ttl::before{content:"";display:block;width:14px;height:1.5px;background:var(--gold);margin:0 auto 5px}
.ttl.left::before{margin:0 0 5px}
.sub{position:absolute;left:0;right:0;text-align:center;font-size:3.6px;color:var(--muted)}
.p{font-size:3.6px;line-height:5px;color:#777}
.h{font-size:4.6px;font-weight:600;color:var(--ink)}
.gold{color:var(--gold)}
.foot{position:absolute;left:11px;right:11px;bottom:7px;display:flex;justify-content:space-between;align-items:center;font-size:4px;color:var(--gold)}
.foot span:last-child{color:var(--muted)}
.mk{width:10px;height:10px;border:1.2px solid var(--gold);display:block}
.dark .foot span{color:#fff}
.ph{position:absolute}
.card{position:absolute;background:#fff;box-shadow:0 2px 6px rgba(0,0,0,.09)}
.stat{font-size:10px;font-weight:600;color:var(--gold)}
.lbl{font-size:4px;color:#555}
.brand{font-size:6px;font-weight:600;color:var(--gold);letter-spacing:.6px;display:flex;align-items:center;gap:4px}
.brand i{width:8px;height:8px;background:var(--gold);display:block}
.bar{position:absolute;height:4px}
.icons{position:absolute;left:16px;right:16px;top:14px;bottom:14px;
  background-image:radial-gradient(circle,transparent 0 3.2px,var(--gold) 3.4px 4.6px,transparent 4.9px);
  background-size:24px 32.5px}
ul.dots{list-style:none}
ul.dots li{font-size:3.4px;line-height:5px;color:#777}
ul.dots li::before{content:"• ";color:var(--gold)}
</style>
</head>
<body>
<div class="board">

<!-- 1 cover dark -->
<section class="slide dark c1 r1">
  <div class="abs" style="left:0;right:0;top:64px;display:flex;justify-content:center"><div class="brand"><i></i>NIVEL CREST</div></div>
  <div class="abs" style="left:0;right:0;top:96px;text-align:center;font-size:12px;font-weight:600;color:#9a9a9a">Presentation Title Goes Here</div>
  <div class="abs gold" style="left:0;right:0;top:116px;text-align:center;font-size:5px">Credential Subtitle Presentation</div>
  <div class="abs" style="left:0;right:0;top:149px;text-align:center;font-size:6px;font-weight:700">Mr. Mark <span class="gold">Renly</span></div>
  <div class="foot" style="bottom:12px;left:18px;right:18px"><span>July 2023</span><span>nivelcrest.com</span></div>
</section>

<!-- 2 cover dark alt -->
<section class="slide dark c2 r1" style="background:linear-gradient(120deg,#0b0b0b 55%,#262626 75%,#0b0b0b)">
  <div class="abs" style="left:18px;top:50px"><div class="brand"><i></i>NIVEL CREST</div></div>
  <div class="abs" style="left:18px;top:90px;font-size:11px;font-weight:600">Presentation Title Goes Here</div>
  <div class="abs gold" style="left:18px;top:107px;font-size:5px">Credential Subtitle Presentation</div>
  <div class="abs" style="left:18px;top:143px;font-size:6px;font-weight:700">Mr. Mark <span class="gold">Renly</span></div>
  <div class="foot" style="bottom:12px;left:18px;right:18px"><span>July 2023</span><span></span></div>
</section>

<!-- 3 cover light -->
<section class="slide c3 r1">
  <div class="abs" style="left:0;right:0;top:64px;display:flex;justify-content:center"><div class="brand"><i></i>NIVEL CREST</div></div>
  <div class="abs" style="left:0;right:0;top:96px;text-align:center;font-size:12px;font-weight:600">Presentation Title Goes Here</div>
  <div class="abs gold" style="left:0;right:0;top:116px;text-align:center;font-size:5px">Credential Subtitle Presentation</div>
  <div class="abs" style="left:0;right:0;top:149px;text-align:center;font-size:6px;font-weight:700">Mr. Mark <span class="gold">Renly</span></div>
  <div class="foot" style="bottom:12px;left:18px;right:18px;color:#555"><span>July 2023</span><span style="color:#555">nivelcrest.com</span></div>
</section>

<!-- 4 presentation list -->
<section class="slide c4 r1">
  <div class="ttl" style="top:18px">Presentation <em>List</em></div>
  <div class="sub" style="top:38px">Here Our Credential Subtitle</div>
  <div class="abs" style="left:50px;top:68px;width:118px;font-size:4px;font-weight:600">
    <div style="display:flex;justify-content:space-between;border-bottom:.6px solid #bbb;padding-bottom:2px;margin-bottom:22px"><span>COVER SLIDES</span><span>01</span></div>
    <div style="display:flex;justify-content:space-between;border-bottom:.6px solid var(--gold);padding-bottom:2px;margin-bottom:22px;color:var(--gold)"><span>PRESENTATION LIST</span><span>03</span></div>
    <div style="display:flex;justify-content:space-between;border-bottom:.6px solid #bbb;padding-bottom:2px;margin-bottom:22px"><span>ABOUT US</span><span>04</span></div>
    <div style="display:flex;justify-content:space-between;border-bottom:.6px solid #bbb;padding-bottom:2px"><span>OUR MISSIONS &amp; VISION</span><span>06</span></div>
  </div>
  <div class="abs" style="left:218px;top:68px;width:118px;font-size:4px;font-weight:600">
    <div style="display:flex;justify-content:space-between;border-bottom:.6px solid #bbb;padding-bottom:2px;margin-bottom:22px"><span>INFOGRAPH ONE</span><span>07</span></div>
    <div style="display:flex;justify-content:space-between;border-bottom:.6px solid #bbb;padding-bottom:2px;margin-bottom:22px"><span>INFOGRAPH TWO</span><span>08</span></div>
    <div style="display:flex;justify-content:space-between;border-bottom:.6px solid #bbb;padding-bottom:2px;margin-bottom:22px"><span>INFOGRAPH THREE</span><span>09</span></div>
    <div style="display:flex;justify-content:space-between;border-bottom:.6px solid #bbb;padding-bottom:2px"><span>CLOSING SLIDES</span><span>10</span></div>
  </div>
  <div class="foot"><span>nivelcrest.com</span><i class="mk"></i><span>page | 4</span></div>
</section>

<!-- 5 vision -->
<section class="slide c5 r1">
  <div class="ttl" style="top:18px">Our <em>Vision</em></div>
  <div class="sub" style="top:38px">Here Our Credential Subtitle</div>
  <div class="abs" style="left:48px;top:62px;width:290px;height:102px;background:var(--gold-grad);box-shadow:0 3px 8px rgba(0,0,0,.15);display:flex;align-items:center;justify-content:center;text-align:center;padding:0 26px;font-size:6px;font-style:italic;line-height:10px;color:#fff">Our planning team reviews every stage of a build, from the first sketch to the final handover, so builders can cut waste and keep projects on budget and on time.</div>
  <div class="foot"><span>nivelcrest.com</span><i class="mk"></i><span>page | 5</span></div>
</section>

<!-- 6 mission -->
<section class="slide c6 r1">
  <div class="ttl" style="top:20px">Our <em>Mission</em></div>
  <div class="abs" style="left:22px;top:66px;width:342px;display:grid;grid-template-columns:repeat(3,1fr);row-gap:22px;column-gap:14px;text-align:center">
    <div><div class="lbl">Mission One</div><p class="p" style="margin-top:4px">Plan each build step early and clearly so costs stay low.</p></div>
    <div><div class="lbl">Mission Two</div><p class="p" style="margin-top:4px">Plan each build step early and clearly so costs stay low.</p></div>
    <div><div class="lbl">Mission Three</div><p class="p" style="margin-top:4px">Plan each build step early and clearly so costs stay low.</p></div>
    <div><div class="lbl">Mission Four</div><p class="p" style="margin-top:4px">Plan each build step early and clearly so costs stay low.</p></div>
    <div><div class="lbl">Mission Five</div><p class="p" style="margin-top:4px">Plan each build step early and clearly so costs stay low.</p></div>
    <div><div class="lbl">Mission Six</div><p class="p" style="margin-top:4px">Plan each build step early and clearly so costs stay low.</p></div>
  </div>
  <div class="foot"><span>nivelcrest.com</span><i class="mk"></i><span>page | 6</span></div>
</section>

<!-- 7 legacy -->
<section class="slide c1 r2">
  <div class="ph" role="img" aria-label="Photo of a tall brick apartment tower" style="left:40px;top:42px;width:105px;height:128px;background:linear-gradient(160deg,#f3ece6,#c98f76 60%,#a56452)"></div>
  <div class="ttl left" style="left:178px;top:54px">Nivel Crest <em>Legacy</em></div>
  <p class="p abs" style="left:178px;top:86px;width:160px">We help builders plan smarter, cutting costs through clear and careful scheduling.</p>
  <div class="card" style="left:186px;top:124px;width:30px;height:30px;text-align:center;padding-top:5px"><div class="stat" style="font-size:8px">14+</div><div class="lbl" style="font-size:3px">Partner</div></div>
  <div class="abs" style="left:218px;top:116px;width:38px;height:40px;background:var(--gold-grad);text-align:center;padding-top:9px;color:#fff"><div style="font-size:8px;font-weight:600">200+</div><div style="font-size:3px">Satisfy Client</div></div>
  <div class="card" style="left:258px;top:124px;width:30px;height:30px;text-align:center;padding-top:5px"><div class="stat" style="font-size:8px">320+</div><div class="lbl" style="font-size:3px">Employee</div></div>
  <div class="foot"><span>nivelcrest.com</span><i class="mk"></i><span>page | 7</span></div>
</section>

<!-- 8 pictures -->
<section class="slide c2 r2">
  <div class="ttl" style="top:20px">Our <em>Pictures</em></div>
  <div class="sub" style="top:40px">Here Our Credential Subtitle</div>
  <div class="ph" role="img" aria-label="Photo of a modern open office interior" style="left:26px;top:56px;width:88px;height:70px;background:linear-gradient(180deg,#4a4a4a,#8c8c8c 60%,#3a3a3a)"></div>
  <div class="ph" role="img" aria-label="Photo of a person on an orange lit stairway" style="left:148px;top:56px;width:88px;height:70px;background:linear-gradient(135deg,#c65a1c,#e49a55 55%,#f1e6d8)"></div>
  <div class="ph" role="img" aria-label="Photo of a white house among autumn trees" style="left:270px;top:56px;width:88px;height:70px;background:linear-gradient(180deg,#c9b27e,#e7e1d6 50%,#8f7a45)"></div>
  <div class="abs" style="left:26px;top:133px;width:88px;text-align:center"><div class="h" style="font-size:4px">Picture One</div><p class="p" style="margin-top:3px">Short note on the site shown here for the client.</p></div>
  <div class="abs" style="left:148px;top:133px;width:88px;text-align:center"><div class="h" style="font-size:4px">Picture Two</div><p class="p" style="margin-top:3px">Short note on the site shown here for the client.</p></div>
  <div class="abs" style="left:270px;top:133px;width:88px;text-align:center"><div class="h" style="font-size:4px">Picture Three</div><p class="p" style="margin-top:3px">Short note on the site shown here for the client.</p></div>
  <div class="foot"><span>nivelcrest.com</span><i class="mk"></i><span>page | 8</span></div>
</section>

<!-- 9 legacy stats -->
<section class="slide c3 r2">
  <div class="ttl" style="top:22px">Nivel Crest <em>Legacy</em></div>
  <div class="sub" style="top:42px">Here Our Credential Subtitle</div>
  <p class="p abs" style="left:52px;top:80px;width:284px;text-align:center"><b class="gold">Our story</b> started with one builder who wanted a leaner plan. Since then we have shaped hundreds of schedules, trimmed material waste and guided teams through permits, budgets and site work with calm, clear planning.</p>
  <div class="abs" style="left:30px;top:140px;width:326px;display:flex;justify-content:space-around;text-align:center">
    <div><div class="stat">243</div><div class="lbl">Project Done</div></div>
    <div><div class="stat">232</div><div class="lbl">Satisfy Costumer</div></div>
    <div><div class="stat">37</div><div class="lbl">Global PartnerSystem</div></div>
    <div><div class="stat">32+</div><div class="lbl">Certifications Company</div></div>
  </div>
  <div class="foot"><span>nivelcrest.com</span><i class="mk"></i><span>page | 9</span></div>
</section>

<!-- 10 analyse chart -->
<section class="slide c4 r2">
  <div class="ttl" style="top:20px">Analyse <em>Chart</em></div>
  <div class="card" style="left:18px;top:58px;width:140px;height:122px">
    <div class="h abs" style="left:6px;top:6px;font-size:4px">Finding Chart</div>
    <svg class="abs" style="left:0;top:0" width="140" height="122">
      <g font-size="3.4" fill="#888" font-family="Poppins,sans-serif">
        <text x="18" y="36">Data Five</text><text x="18" y="51">Data Four</text><text x="10" y="66">Data Three</text><text x="18" y="81">Data Two</text><text x="18" y="96">Data One</text>
        <text x="60" y="112">0</text><text x="88" y="112">100</text><text x="116" y="112">200</text>
      </g>
      <rect x="62" y="32" width="16" height="4" fill="#7d8aa8"/>
      <rect x="62" y="47" width="22" height="4" fill="#3d4863"/>
      <rect x="62" y="62" width="38" height="4" fill="#c48f3f"/>
      <rect x="62" y="77" width="20" height="4" fill="#a9b3c8"/>
      <rect x="62" y="92" width="48" height="4" fill="#3d4863"/>
    </svg>
  </div>
  <div class="card" style="left:166px;top:58px;width:204px;height:122px;padding:7px 10px">
    <div class="h" style="font-size:3.8px">Analyse One:</div><p class="p">Costs on site rose where the plan had no buffer for late supply. A clear order list now keeps steel and timber on time.</p>
    <div class="h" style="font-size:3.8px;margin-top:4px">Analyse Two:</div><p class="p">Crew hours were lost between trades. Staggered starts let each team work without waiting on the last one.</p>
    <div class="h" style="font-size:3.8px;margin-top:4px">Analyse Three:</div><p class="p">Design changes late in the build cost most. A fixed review point before ground work helps lock scope.</p>
  </div>
  <div class="foot"><span>nivelcrest.com</span><i class="mk"></i><span>page | 10</span></div>
</section>

<!-- 11 company overview -->
<section class="slide c5 r2">
  <div class="abs" style="left:0;top:42px;width:170px;height:130px;background:var(--gold-grad);border-top-right-radius:40px"></div>
  <div class="ttl" style="left:210px;right:auto;top:42px;width:170px">Company <em>Overview</em></div>
  <div class="card" style="left:24px;top:76px;width:330px;height:70px"></div>
  <div class="ph" role="img" aria-label="Photo of an architect at a drawing board" style="left:44px;top:84px;width:52px;height:52px;border-radius:50%;background:linear-gradient(135deg,#6e8aa4,#dcd6cc 60%,#8a6b4c);border:3px solid #fff;box-shadow:0 0 0 1px var(--gold)"></div>
  <div class="abs" style="left:110px;top:88px;display:flex;gap:20px">
    <div><div style="width:7px;height:7px;border:1px solid var(--gold);border-radius:50%;margin-bottom:4px"></div><div class="stat" style="font-size:8px">8 Hour</div><div class="lbl" style="font-size:3px">Working Hour</div></div>
    <div><div style="width:7px;height:6px;border:1px solid var(--gold);margin-bottom:5px"></div><div class="stat" style="font-size:8px">$6K</div><div class="lbl" style="font-size:3px">Weekly Profit</div></div>
    <div><div style="width:7px;height:6px;border-bottom:1px solid var(--gold);margin-bottom:5px"></div><div class="stat" style="font-size:8px">145</div><div class="lbl" style="font-size:3px">Consultant</div></div>
    <div><div style="width:7px;height:7px;border:1px solid var(--gold);border-radius:50%;margin-bottom:4px"></div><div class="stat" style="font-size:8px">32 Brands</div><div class="lbl" style="font-size:3px">Global Brands</div></div>
  </div>
  <div class="foot"><span>nivelcrest.com</span><i class="mk"></i><span>page | 11</span></div>
</section>

<!-- 12 swot -->
<section class="slide c6 r2">
  <div class="ttl" style="top:22px">S.W.O.T <em>Analayse</em></div>
  <p class="p abs" style="left:52px;top:58px;width:282px;text-align:center"><b>Our review</b> sets out where a build plan is strong, where it is thin, which openings exist and which risks to watch before work on site begins.</p>
  <div class="abs" style="left:20px;top:104px;width:346px;display:grid;grid-template-columns:repeat(4,1fr);gap:6px">
    <div class="card" style="position:relative;height:58px;padding:6px"><div class="lbl">Strenght</div><p class="p" style="font-size:3px;margin-top:3px">1. Clear cost plan<br>2. Fast site review<br>3. Skilled planners<br>4. Strong network</p></div>
    <div style="height:58px;padding:6px;background:var(--gold-grad);color:#fff"><div style="font-size:4px">Weakness</div><p class="p" style="font-size:3px;margin-top:3px;color:#fff">1. Small team size<br>2. New in region<br>3. Long onboarding<br>4. Few local ties</p></div>
    <div class="card" style="position:relative;height:58px;padding:6px"><div class="lbl">Opportunity</div><p class="p" style="font-size:3px;margin-top:3px">1. Rising build costs<br>2. Green standards<br>3. Digital planning<br>4. New partners</p></div>
    <div class="card" style="position:relative;height:58px;padding:6px"><div class="lbl">Thread</div><p class="p" style="font-size:3px;margin-top:3px">1. Price pressure<br>2. Supply delays<br>3. Rule changes<br>4. New rivals</p></div>
  </div>
  <div class="foot"><span>nivelcrest.com</span><i class="mk"></i><span>page | 12</span></div>
</section>

<!-- 13 business strategy -->
<section class="slide c1 r3">
  <div class="ttl left" style="left:20px;top:12px">Business <em>Strategy</em></div>
  <div class="abs" style="left:20px;top:50px;width:346px;display:grid;grid-template-columns:repeat(3,1fr);gap:10px 12px">
    <div style="height:55px;background:var(--gold-grad);padding:14px 8px;color:#fff"><div style="font-size:3.8px;font-weight:600">Strategy Company One</div><p class="p" style="color:#fff;font-size:3.2px">Plan scope first, then book crews and stock to match.</p></div>
    <div class="card" style="position:relative;height:55px;padding:14px 8px"><div class="h" style="font-size:3.8px">Strategy Company Two</div><p class="p" style="font-size:3.2px">Plan scope first, then book crews and stock to match.</p></div>
    <div class="card" style="position:relative;height:55px;padding:14px 8px"><div class="h" style="font-size:3.8px">Strategy Company Three</div><p class="p" style="font-size:3.2px">Plan scope first, then book crews and stock to match.</p></div>
    <div class="card" style="position:relative;height:55px;padding:14px 8px"><div class="h" style="font-size:3.8px">Strategy Company Four</div><p class="p" style="font-size:3.2px">Plan scope first, then book crews and stock to match.</p></div>
    <div class="card" style="position:relative;height:55px;padding:14px 8px"><div class="h" style="font-size:3.8px">Strategy Company Five</div><p class="p" style="font-size:3.2px">Plan scope first, then book crews and stock to match.</p></div>
    <div class="card" style="position:relative;height:55px;padding:14px 8px"><div class="h" style="font-size:3.8px">Strategy Company Six</div><p class="p" style="font-size:3.2px">Plan scope first, then book crews and stock to match.</p></div>
  </div>
  <div class="foot"><span>nivelcrest.com</span><i class="mk"></i><span>page | 13</span></div>
</section>

<!-- 14 building analytic -->
<section class="slide c2 r3">
  <div class="ph" role="img" aria-label="Photo of a classic corner apartment building" style="left:22px;top:0;width:122px;height:172px;background:linear-gradient(180deg,#b9c9d6,#ddd3c2 45%,#8c7a64)"></div>
  <div class="ttl left" style="left:194px;top:22px">Building <em>Analytic</em></div>
  <p class="p abs" style="left:194px;top:48px;width:160px">We check each structure for cost risk before work starts.</p>
  <svg class="abs" style="left:140px;top:70px" width="100" height="90"><g stroke="#c48f3f" stroke-width=".7" fill="#c48f3f"><line x1="0" y1="8" x2="50" y2="8"/><circle cx="2" cy="8" r="1.3"/><line x1="0" y1="41" x2="65" y2="41"/><circle cx="2" cy="41" r="1.3"/><line x1="0" y1="74" x2="80" y2="74"/><circle cx="2" cy="74" r="1.3"/></g></svg>
  <div class="abs" style="left:194px;top:76px;width:140px"><div class="h gold" style="font-size:3.8px">Building Analytic One</div><p class="p">Site load and soil checked early.</p></div>
  <div class="abs" style="left:209px;top:109px;width:140px"><div class="h gold" style="font-size:3.8px">Building Analytic Two</div><p class="p">Frame and shell cost mapped out.</p></div>
  <div class="abs" style="left:224px;top:142px;width:140px"><div class="h gold" style="font-size:3.8px">Building Analytic Three</div><p class="p">Finish work timed to stock supply.</p></div>
  <div class="foot"><span>nivelcrest.com</span><i class="mk"></i><span>page | 14</span></div>
</section>

<!-- 15 building plan -->
<section class="slide c3 r3">
  <div class="ttl left" style="left:30px;top:36px">Building <em>Plan</em></div>
  <p class="p abs" style="left:30px;top:60px;width:180px">Three stages that turn a draft into a priced and timed build.</p>
  <div class="abs" style="left:30px;top:108px;display:flex;gap:8px">
    <div class="card" style="position:relative;width:72px;height:52px;padding:6px"><div class="h" style="font-size:3.6px">First Building Plan</div><p class="p" style="font-size:3.2px">Scope, site and early cost figures.</p></div>
    <div class="card" style="position:relative;width:72px;height:52px;padding:6px"><div class="h" style="font-size:3.6px">Second Building Plan</div><p class="p" style="font-size:3.2px">Trade order and stock schedule.</p></div>
    <div class="card" style="position:relative;width:72px;height:52px;padding:6px"><div class="h" style="font-size:3.6px">Third Building Plan</div><p class="p" style="font-size:3.2px">Final checks and handover plan.</p></div>
  </div>
  <div class="ph" role="img" aria-label="Photo of a person on an orange lit stairway" style="left:240px;top:0;width:108px;height:58px;background:linear-gradient(135deg,#b7501a,#e49a55 55%,#efe2d2)"></div>
  <div class="ph" role="img" aria-label="Photo looking up at a white high-rise facade" style="left:240px;top:64px;width:108px;height:118px;background:linear-gradient(180deg,#8fb5d8,#e9eef2 60%,#c9ccd0)"></div>
  <div class="foot"><span>nivelcrest.com</span><i class="mk"></i><span>page | 15</span></div>
</section>

<!-- 16 system marketing -->
<section class="slide c4 r3">
  <div class="ph" role="img" aria-label="Photo of a person on an orange lit stairway" style="left:0;top:36px;width:192px;height:138px;background:linear-gradient(135deg,#a8461a,#e18e48 50%,#f2e4d3)"></div>
  <div class="ttl left" style="left:212px;top:32px">System <em>Marketing</em></div>
  <p class="p abs" style="left:212px;top:60px;width:150px">How we reach builders and show the savings we bring.</p>
  <div class="abs" style="left:210px;top:92px;width:156px">
    <div class="h" style="font-size:3.6px">Systems One Marketing</div>
    <ul class="dots"><li>Site visits with cost reviews.</li><li>Case notes from past builds.</li><li>Talks at trade events.</li></ul>
    <div class="h" style="font-size:3.6px;margin-top:6px">Systems Two Marketing</div>
    <ul class="dots"><li>Short guides for new builders.</li><li>Monthly planning letters.</li><li>Free first plan check.</li></ul>
  </div>
  <div class="foot"><span>nivelcrest.com</span><i class="mk"></i><span>page | 16</span></div>
</section>

<!-- 17 our work -->
<section class="slide c5 r3">
  <div class="ph" role="img" aria-label="Photo of a white house with autumn trees" style="left:14px;top:20px;width:80px;height:80px;background:linear-gradient(180deg,#c8a86a,#e8e2d8 55%,#8f7a45)"></div>
  <p class="p abs" style="left:98px;top:44px;width:70px">House plan with stock and crew timing set out.</p>
  <div class="ph" role="img" aria-label="Photo of an old stone building facade" style="left:174px;top:20px;width:80px;height:80px;background:linear-gradient(180deg,#6f5a44,#b19474 60%,#4a3c2f)"></div>
  <p class="p abs" style="left:14px;top:124px;width:72px">Office fit-out planned within a fixed budget.</p>
  <div class="ph" role="img" aria-label="Photo of a modern open office interior" style="left:94px;top:100px;width:80px;height:80px;background:linear-gradient(180deg,#4a4a4a,#8c8c8c 60%,#3a3a3a)"></div>
  <p class="p abs" style="left:180px;top:124px;width:72px">Facade repair staged to keep the site open.</p>
  <div class="ttl left" style="left:268px;top:80px">Our <em style="color:var(--ink)">Work</em></div>
  <p class="p abs" style="left:268px;top:104px;width:104px">Builds where our planning cut cost and time.</p>
  <div class="foot"><span>nivelcrest.com</span><i class="mk"></i><span>page | 17</span></div>
</section>

<!-- 18 company leader -->
<section class="slide c6 r3">
  <div class="ttl" style="top:18px">Company <em>Leader</em></div>
  <div class="abs" style="left:22px;top:52px;width:342px;display:flex;gap:6px">
    <div class="card" style="position:relative;flex:1;height:128px;text-align:center;overflow:hidden"><div style="height:30px;background:var(--gold-grad)"></div><div role="img" aria-label="Portrait of team leader" style="width:34px;height:34px;border-radius:50%;margin:-22px auto 0;background:linear-gradient(135deg,#8ab6d8,#3f6e9c);border:2px solid #fff"></div><div class="h" style="margin-top:3px;font-size:4.6px">Dara</div><div class="lbl" style="font-size:3px">Manager of Lorem</div><ul class="dots" style="text-align:left;padding:6px 6px 0"><li>Sets the cost plan</li><li>Leads site review</li><li>Signs off budgets</li></ul></div>
    <div class="card" style="position:relative;flex:1;height:128px;text-align:center;overflow:hidden"><div style="height:30px;background:var(--gold-grad)"></div><div role="img" aria-label="Portrait of team leader" style="width:34px;height:34px;border-radius:50%;margin:-22px auto 0;background:linear-gradient(135deg,#8ab6d8,#3f6e9c);border:2px solid #fff"></div><div class="h" style="margin-top:3px;font-size:4.6px">Lina</div><div class="lbl" style="font-size:3px">Manager of Lorem</div><ul class="dots" style="text-align:left;padding:6px 6px 0"><li>Sets the cost plan</li><li>Leads site review</li><li>Signs off budgets</li></ul></div>
    <div class="card" style="position:relative;flex:1;height:128px;text-align:center;overflow:hidden"><div style="height:30px;background:var(--gold-grad)"></div><div role="img" aria-label="Portrait of team leader" style="width:34px;height:34px;border-radius:50%;margin:-22px auto 0;background:linear-gradient(135deg,#8ab6d8,#3f6e9c);border:2px solid #fff"></div><div class="h" style="margin-top:3px;font-size:4.6px">Omar</div><div class="lbl" style="font-size:3px">Manager of Lorem</div><ul class="dots" style="text-align:left;padding:6px 6px 0"><li>Sets the cost plan</li><li>Leads site review</li><li>Signs off budgets</li></ul></div>
    <div class="card" style="position:relative;flex:1;height:128px;text-align:center;overflow:hidden"><div style="height:30px;background:var(--gold-grad)"></div><div role="img" aria-label="Portrait of team leader" style="width:34px;height:34px;border-radius:50%;margin:-22px auto 0;background:linear-gradient(135deg,#8ab6d8,#3f6e9c);border:2px solid #fff"></div><div class="h" style="margin-top:3px;font-size:4.6px">Mira</div><div class="lbl" style="font-size:3px">Manager of Lorem</div><ul class="dots" style="text-align:left;padding:6px 6px 0"><li>Sets the cost plan</li><li>Leads site review</li><li>Signs off budgets</li></ul></div>
  </div>
  <div class="foot"><span>nivelcrest.com</span><i class="mk"></i><span>page | 18</span></div>
</section>

<!-- 19 member team -->
<section class="slide c1 r4">
  <div class="ttl" style="top:18px">Member <em>Team</em></div>
  <div class="abs" style="left:32px;top:50px;width:156px;height:60px;background:var(--gold-grad);box-shadow:0 2px 6px rgba(0,0,0,.12)"></div>
  <div role="img" aria-label="Portrait of marketing manager" class="abs" style="left:38px;top:58px;width:44px;height:44px;border-radius:50%;background:linear-gradient(135deg,#7fa9d6,#2d4f8a);border:2px solid #fff"></div>
  <div class="abs" style="left:100px;top:70px;color:#fff"><div style="font-size:7px;font-weight:600">Nora Hale</div><div style="font-size:4px">Marketing Manager</div></div>
  <div class="card" style="left:198px;top:50px;width:70px;height:60px;text-align:center;padding-top:4px"><div role="img" aria-label="Portrait of team member" style="width:30px;height:30px;border-radius:50%;margin:0 auto;background:linear-gradient(135deg,#e46b5c,#7b2c28)"></div><div class="h" style="font-size:3.8px;margin-top:3px">Ben Avery</div><div class="lbl" style="font-size:3px">Manager Marketing</div></div>
  <div class="card" style="left:278px;top:50px;width:70px;height:60px;text-align:center;padding-top:4px"><div role="img" aria-label="Portrait of team member" style="width:30px;height:30px;border-radius:50%;margin:0 auto;background:linear-gradient(135deg,#c9c4bd,#5d5750)"></div><div class="h" style="font-size:3.8px;margin-top:3px">Tom Brask</div><div class="lbl" style="font-size:3px">Manager Service</div></div>
  <div class="abs" style="left:32px;top:118px;display:flex;gap:10px">
    <div class="card" style="position:relative;width:72px;height:60px;text-align:center;padding-top:4px"><div role="img" aria-label="Portrait of team member" style="width:30px;height:30px;border-radius:50%;margin:0 auto;background:linear-gradient(135deg,#b79a7c,#4e3b2d)"></div><div class="h" style="font-size:3.8px;margin-top:3px">Ada Wren</div><div class="lbl" style="font-size:3px">Staff Marketing</div></div>
    <div class="card" style="position:relative;width:72px;height:60px;text-align:center;padding-top:4px"><div role="img" aria-label="Portrait of team member" style="width:30px;height:30px;border-radius:50%;margin:0 auto;background:linear-gradient(135deg,#5ab6c9,#2a4d59)"></div><div class="h" style="font-size:3.8px;margin-top:3px">Cleo Marsh</div><div class="lbl" style="font-size:3px">Staff Marketing</div></div>
    <div class="card" style="position:relative;width:72px;height:60px;text-align:center;padding-top:4px"><div role="img" aria-label="Portrait of team member" style="width:30px;height:30px;border-radius:50%;margin:0 auto;background:linear-gradient(135deg,#d7c3b3,#7a5b4a)"></div><div class="h" style="font-size:3.8px;margin-top:3px">Iris Vale</div><div class="lbl" style="font-size:3px">Staff Marketing</div></div>
    <div class="card" style="position:relative;width:72px;height:60px;text-align:center;padding-top:4px"><div role="img" aria-label="Portrait of team member" style="width:30px;height:30px;border-radius:50%;margin:0 auto;background:linear-gradient(135deg,#c99a77,#5e3b26)"></div><div class="h" style="font-size:3.8px;margin-top:3px">June Holt</div><div class="lbl" style="font-size:3px">Staff Service</div></div>
  </div>
  <div class="foot"><span>nivelcrest.com</span><i class="mk"></i><span>page | 19</span></div>
</section>

<!-- 20 timeline -->
<section class="slide c2 r4">
  <div class="ttl left" style="left:18px;top:12px">Project <em>Timeline</em></div>
  <svg class="abs" style="left:0;top:60px" width="386" height="90">
    <line x1="18" y1="52" x2="386" y2="52" stroke="#999" stroke-width=".6"/>
    <g fill="#c48f3f"><circle cx="44" cy="52" r="1.6"/><circle cx="128" cy="52" r="1.6"/><circle cx="212" cy="52" r="1.6"/><circle cx="296" cy="52" r="1.6"/></g>
    <g fill="#e0b552" stroke="#f3e3be" stroke-width="2"><circle cx="44" cy="22" r="7"/><circle cx="212" cy="22" r="8"/><circle cx="128" cy="82" r="7"/><circle cx="296" cy="82" r="7"/></g>
  </svg>
  <div class="abs" style="left:127px;top:72px;width:75px"><div class="h" style="font-size:4px">May 2023</div><p class="p">Site survey and first cost draft.</p></div>
  <div class="abs" style="left:297px;top:72px;width:75px"><div class="h" style="font-size:4px">July 2023</div><p class="p">Trade order and stock booking.</p></div>
  <div class="abs" style="left:42px;top:120px;width:75px"><div class="h" style="font-size:4px">March 2023</div><p class="p">Brief agreed and team set up.</p></div>
  <div class="abs" style="left:212px;top:120px;width:75px"><div class="h" style="font-size:4px">May 2023</div><p class="p">Budget review with the builder.</p></div>
  <div class="foot"><span>nivelcrest.com</span><i class="mk"></i><span>page | 20</span></div>
</section>

<!-- 21 timeline 2 -->
<section class="slide c3 r4">
  <div class="ttl left" style="left:18px;top:12px">Project <em>Timeline</em></div>
  <svg class="abs" style="left:0;top:60px" width="386" height="90">
    <line x1="0" y1="52" x2="386" y2="52" stroke="#999" stroke-width=".6"/>
    <g fill="#c48f3f"><circle cx="62" cy="52" r="1.6"/><circle cx="182" cy="52" r="1.6"/><circle cx="298" cy="52" r="1.6"/></g>
    <g fill="#e0b552" stroke="#f3e3be" stroke-width="2"><circle cx="182" cy="24" r="11"/><circle cx="62" cy="80" r="7"/><circle cx="298" cy="80" r="7"/></g>
  </svg>
  <div class="abs" style="left:62px;top:72px;width:80px"><div class="h" style="font-size:4px">July 2023</div><p class="p">Ground work and frame start.</p></div>
  <div class="abs" style="left:296px;top:72px;width:80px"><div class="h" style="font-size:4px">September 2023</div><p class="p">Shell closed, finish work begins.</p></div>
  <div class="abs" style="left:180px;top:120px;width:80px"><div class="h" style="font-size:4px">August 2023</div><p class="p">Mid-build cost check on site.</p></div>
  <div class="foot"><span>nivelcrest.com</span><i class="mk"></i><span>page | 21</span></div>
</section>

<!-- 22 circle graph -->
<section class="slide c4 r4">
  <div class="ttl left" style="left:24px;top:56px;line-height:1.5">Circle Graph<br><em>Analyse</em></div>
  <p class="p abs" style="left:24px;top:120px;width:110px">Share of monthly work by phase for the first half year of the build.</p>
  <svg class="abs" style="left:150px;top:48px" width="90" height="100" viewBox="0 0 90 100">
    <circle cx="42" cy="42" r="32" fill="none" stroke="#eadbc4" stroke-width="9"/>
    <circle cx="42" cy="42" r="32" fill="none" stroke="#c48f3f" stroke-width="9" stroke-dasharray="70 201" transform="rotate(-90 42 42)"/>
    <circle cx="42" cy="42" r="32" fill="none" stroke="#d9ad5b" stroke-width="9" stroke-dasharray="50 201" stroke-dashoffset="-70" transform="rotate(-90 42 42)"/>
    <circle cx="42" cy="42" r="32" fill="none" stroke="#3d4863" stroke-width="9" stroke-dasharray="25 201" stroke-dashoffset="-120" transform="rotate(-90 42 42)"/>
    <circle cx="42" cy="42" r="32" fill="none" stroke="#b88a5a" stroke-width="9" stroke-dasharray="40 201" stroke-dashoffset="-150" transform="rotate(-90 42 42)"/>
    <g font-size="3" fill="#c48f3f" font-family="Poppins,sans-serif"><text x="2" y="96">● Jan ● Feb ● Mar ● Apr ● May ● Jun</text></g>
  </svg>
  <div class="abs" style="left:278px;top:52px;width:84px;height:42px;border:.8px solid #ccc;padding:4px 6px"><div class="lbl" style="font-size:3px">July</div><div style="text-align:right;font-size:10px;margin-top:8px">$5700</div></div>
  <div class="abs" style="left:278px;top:102px;width:84px;height:42px;border:.8px solid var(--gold);padding:4px 6px"><div class="lbl" style="font-size:3px">March</div><div class="gold" style="text-align:right;font-size:10px;margin-top:8px">$7600</div></div>
  <div class="foot"><span>nivelcrest.com</span><i class="mk"></i><span>page | 22</span></div>
</section>

<!-- 23 infograph hexes -->
<section class="slide c5 r4">
  <div class="ttl" style="top:22px">Infograph</div>
  <svg class="abs" style="left:10px;top:70px" width="366" height="46">
    <g fill="#fff" stroke="#e6d6bd" stroke-width="1">
      <polygon points="40,2 58,12 58,34 40,44 22,34 22,12"/><polygon points="108,2 126,12 126,34 108,44 90,34 90,12"/><polygon points="176,2 194,12 194,34 176,44 158,34 158,12"/><polygon points="244,2 262,12 262,34 244,44 226,34 226,12"/><polygon points="312,2 330,12 330,34 312,44 294,34 294,12"/>
    </g>
    <g stroke="#c48f3f" stroke-width=".8"><line x1="62" y1="23" x2="86" y2="23"/><line x1="130" y1="23" x2="154" y2="23"/><line x1="198" y1="23" x2="222" y2="23"/><line x1="266" y1="23" x2="290" y2="23"/></g>
    <g font-size="5" fill="#c48f3f" text-anchor="middle" font-family="Poppins,sans-serif"><text x="40" y="25">Step 1</text><text x="108" y="25">Step 2</text><text x="176" y="25">Step 3</text><text x="244" y="25">Step 4</text><text x="312" y="25">Step 5</text></g>
  </svg>
  <div class="abs" style="left:18px;top:138px;width:350px;display:flex;justify-content:space-between;text-align:center">
    <div style="width:62px"><div class="h" style="font-size:3.4px">Marketing Step</div><p class="p" style="font-size:3.2px">Reach the right builder.</p></div>
    <div style="width:62px"><div class="h" style="font-size:3.4px">Production Step</div><p class="p" style="font-size:3.2px">Draft the cost plan.</p></div>
    <div style="width:62px"><div class="h" style="font-size:3.4px">R&amp;D Step</div><p class="p" style="font-size:3.2px">Test cheaper methods.</p></div>
    <div style="width:62px"><div class="h" style="font-size:3.4px">Vendor Step</div><p class="p" style="font-size:3.2px">Book stock and crews.</p></div>
    <div style="width:62px"><div class="h" style="font-size:3.4px">Supplier Step</div><p class="p" style="font-size:3.2px">Track every delivery.</p></div>
  </div>
  <div class="foot"><span>nivelcrest.com</span><i class="mk"></i><span>page | 23</span></div>
</section>

<!-- 24 infograph circles -->
<section class="slide c6 r4">
  <div class="ttl" style="top:18px">Infograph</div>
  <svg class="abs" style="left:0;top:56px" width="386" height="130">
    <g stroke="#3d4863" stroke-width="3"><line x1="70" y1="46" x2="100" y2="80"/><line x1="100" y1="80" x2="140" y2="44"/><line x1="140" y1="44" x2="180" y2="80"/><line x1="180" y1="80" x2="220" y2="44"/><line x1="220" y1="44" x2="260" y2="80"/><line x1="260" y1="80" x2="300" y2="44"/></g>
    <g fill="#fff" stroke="#f0dcb5" stroke-width="3"><circle cx="62" cy="40" r="14"/><circle cx="140" cy="36" r="14"/><circle cx="218" cy="36" r="14"/><circle cx="300" cy="40" r="14"/><circle cx="100" cy="82" r="12"/><circle cx="180" cy="82" r="12"/><circle cx="260" cy="82" r="12"/></g>
    <g fill="none" stroke="#c48f3f" stroke-width=".9"><rect x="58" y="36" width="8" height="8"/><rect x="136" y="32" width="8" height="8"/><circle cx="218" cy="36" r="4"/><rect x="296" y="36" width="8" height="8"/><circle cx="100" cy="82" r="3"/><circle cx="180" cy="82" r="3"/><circle cx="260" cy="82" r="3"/></g>
  </svg>
  <div class="abs" style="left:30px;top:60px;width:330px;display:flex;justify-content:space-between;text-align:center"><p class="p" style="width:60px">Brief and scope set</p><p class="p" style="width:60px">Site and soil check</p><p class="p" style="width:60px">Cost plan drafted</p><p class="p" style="width:60px">Crews and stock set</p></div>
  <div class="abs" style="left:72px;top:160px;width:220px;display:flex;justify-content:space-between;text-align:center"><p class="p" style="width:60px">Budget approved</p><p class="p" style="width:60px">Build on site</p><p class="p" style="width:60px">Final handover</p></div>
  <div class="foot"><span>nivelcrest.com</span><i class="mk"></i><span>page | 24</span></div>
</section>

<!-- 25 pricing -->
<section class="slide c1 r5">
  <div class="ttl" style="top:20px">Pricing <em>Table</em></div>
  <div class="abs" style="left:28px;top:52px;width:330px;display:flex;gap:10px">
    <div class="card" style="position:relative;flex:1;height:128px;text-align:center;padding-top:14px"><div style="width:8px;height:8px;border:1px solid var(--gold);margin:0 auto 6px"></div><div class="stat" style="font-size:9px">$300</div><div class="lbl">Starter Package</div><ul class="dots" style="text-align:left;padding:8px 8px 0"><li>One site cost review</li><li>Basic build schedule</li><li>Email support</li></ul><div style="margin:8px auto 0;width:36px;height:8px;border-radius:4px;background:var(--gold-grad);font-size:3px;color:#fff;line-height:8px">Learn More</div></div>
    <div class="card" style="position:relative;flex:1;height:128px;text-align:center;padding-top:14px"><div style="width:8px;height:8px;border:1px solid var(--gold);margin:0 auto 6px"></div><div class="stat" style="font-size:9px">$800</div><div class="lbl">Medium Package</div><ul class="dots" style="text-align:left;padding:8px 8px 0"><li>Full cost plan</li><li>Trade timing plan</li><li>Monthly site visit</li></ul><div style="margin:8px auto 0;width:36px;height:8px;border-radius:4px;background:var(--gold-grad);font-size:3px;color:#fff;line-height:8px">Learn More</div></div>
    <div class="card" style="position:relative;flex:1;height:128px;text-align:center;padding-top:14px"><div style="width:8px;height:8px;border:1px solid var(--gold);margin:0 auto 6px"></div><div class="stat" style="font-size:9px">$1,400</div><div class="lbl">Pro Package</div><ul class="dots" style="text-align:left;padding:8px 8px 0"><li>Plan and site lead</li><li>Supplier handling</li><li>Weekly reporting</li></ul><div style="margin:8px auto 0;width:36px;height:8px;border-radius:4px;background:var(--gold-grad);font-size:3px;color:#fff;line-height:8px">Learn More</div></div>
  </div>
  <div class="foot"><span>nivelcrest.com</span><i class="mk"></i><span>page | 25</span></div>
</section>

<!-- 26 monthly chart -->
<section class="slide c2 r5">
  <div class="ttl" style="left:0;right:0;top:22px;width:386px;text-align:center;padding-right:0">Monthly Chart</div>
  <svg class="abs" style="left:30px;top:70px" width="230" height="100">
    <polyline points="10,58 52,40 90,74 130,60 168,72 210,62" fill="none" stroke="#c48f3f" stroke-width="1"/>
    <g fill="#c48f3f" font-size="4" font-family="Poppins,sans-serif"><circle cx="10" cy="58" r="1.4"/><circle cx="52" cy="40" r="1.4"/><circle cx="90" cy="74" r="1.4"/><circle cx="130" cy="60" r="1.4"/><circle cx="168" cy="72" r="1.4"/><circle cx="210" cy="62" r="1.4"/>
    <text x="12" y="56">60</text><text x="54" y="38">78</text><text x="92" y="72">49</text><text x="132" y="58">60</text><text x="170" y="70">49</text><text x="212" y="60">56</text></g>
    <g fill="#aaa" font-size="3.4" font-family="Poppins,sans-serif"><text x="6" y="96">JAN</text><text x="48" y="96">FEB</text><text x="86" y="96">MARC</text><text x="126" y="96">APR</text><text x="164" y="96">MAY</text><text x="206" y="96">JUN</text></g>
  </svg>
  <div class="abs" style="left:266px;top:62px;width:100px"><div style="width:14px;height:14px;border-radius:50%;background:var(--gold-grad);color:#fff;font-size:4.4px;text-align:center;line-height:14px">49</div><div style="font-size:7px">May</div><p class="p gold" style="color:var(--gold)">Slow month due to rain delays.</p></div>
  <div class="abs" style="left:266px;top:124px;width:100px"><div style="width:14px;height:14px;border-radius:50%;background:var(--gold-grad);color:#fff;font-size:4.4px;text-align:center;line-height:14px">56</div><div style="font-size:7px">Jun</div><p class="p" style="color:var(--gold)">Pace back up after new crew.</p></div>
  <div class="foot"><span>nivelcrest.com</span><i class="mk"></i><span>page | 26</span></div>
</section>

<!-- 27 marketing table dark -->
<section class="slide dark c3 r5">
  <div class="ttl" style="top:24px;color:var(--gold)">Marketing</div>
  <table class="abs" style="left:54px;top:60px;width:278px;border-collapse:collapse;font-size:3.4px;color:#ddd">
    <tr style="background:#3a3a3a;font-weight:600;color:#fff;height:12px"><td style="padding-left:6px">Data Name</td><td>Number</td><td>Profit Rate</td><td>Option</td><td>Rate</td><td>Performance</td></tr>
    <tr style="height:14.5px"><td style="padding-left:6px">Data One</td><td>5,667</td><td>20.45</td><td>Yes</td><td>70</td><td>3,566</td></tr>
    <tr style="height:14.5px;background:#161616;border-left:1.5px solid #fff"><td style="padding-left:6px">Data Two</td><td>6,5444</td><td>34.5</td><td>Yes</td><td>67</td><td>3,997</td></tr>
    <tr style="height:14.5px"><td style="padding-left:6px">Data Three</td><td>54,333</td><td>56.7</td><td>No</td><td>77</td><td>9,887</td></tr>
    <tr style="height:14.5px;background:#161616;border-left:1.5px solid #fff"><td style="padding-left:6px">Data Four</td><td>7,655</td><td>6.55</td><td>No</td><td>89</td><td>97,666</td></tr>
    <tr style="height:14.5px"><td style="padding-left:6px">Data Five</td><td>7,665</td><td>90</td><td>Yes</td><td>90</td><td>98.9</td></tr>
    <tr style="height:14.5px;background:#161616;border-left:1.5px solid #fff"><td style="padding-left:6px">Data Six</td><td>9,999</td><td>00</td><td>No</td><td>87</td><td>98.7</td></tr>
  </table>
  <div class="foot"><span>nivelcrest.com</span><i class="mk" style="border-color:#fff"></i><span>page | 27</span></div>
</section>

<!-- 28 dashboard 1 -->
<section class="slide c4 r5">
  <div class="ttl" style="top:18px">Dashboard</div>
  <div class="abs" style="left:28px;top:52px;width:330px;display:flex;justify-content:space-between;text-align:center;font-size:3.6px">
    <div><div class="gold">Project Done</div><div style="color:#999;font-size:4.6px">563</div></div>
    <div><div class="gold">Monthly Earning</div><div style="color:#999;font-size:4.6px">$32,470</div></div>
    <div><div class="gold">Costumer Acc</div><div style="color:#999;font-size:4.6px">3,877</div></div>
    <div><div class="gold">Claim</div><div style="color:#999;font-size:4.6px">0</div></div>
  </div>
  <div class="h abs" style="left:28px;top:88px;font-size:3.4px">5 Active Dashboard</div>
  <svg class="abs" style="left:20px;top:98px" width="110" height="90"><g font-size="3.2" fill="#888" font-family="Poppins,sans-serif"><text x="6" y="20">Data Five</text><text x="6" y="32">Data Four</text><text x="2" y="44">Data Three</text><text x="6" y="56">Data Two</text><text x="6" y="68">Data One</text></g>
  <rect x="36" y="16" width="16" height="4" fill="#b47d34"/><rect x="36" y="28" width="24" height="4" fill="#3d4863"/><rect x="36" y="40" width="32" height="4" fill="#f0d488"/><rect x="36" y="52" width="38" height="4" fill="#3d4863"/><rect x="36" y="64" width="42" height="4" fill="#e3c7a2"/></svg>
  <div class="h abs" style="left:138px;top:88px;font-size:3.4px">2 User Per Role</div>
  <svg class="abs" style="left:160px;top:104px" width="50" height="50"><circle cx="25" cy="25" r="16" fill="none" stroke="#f0d488" stroke-width="6"/><circle cx="25" cy="25" r="16" fill="none" stroke="#c48f3f" stroke-width="6" stroke-dasharray="62 100" transform="rotate(-90 25 25)"/></svg>
  <div class="h abs" style="left:258px;top:88px;font-size:3.4px"># Live Profit and Net</div>
  <div class="abs gold" style="left:240px;top:108px;width:120px;text-align:center;font-size:4.6px;font-weight:600">Net Profit &amp; Net sales</div>
  <div class="abs gold" style="left:240px;top:130px;width:120px;text-align:center;font-size:4.4px;font-weight:600">Net profit</div>
  <div class="abs gold" style="left:240px;top:142px;width:120px;text-align:center;font-size:7px">$44.587M</div>
  <div class="abs gold" style="left:240px;top:154px;width:120px;text-align:center;font-size:4px">Net sales = $15M</div>
  <div class="foot"><span>nivelcrest.com</span><i class="mk"></i><span>page | 28</span></div>
</section>

<!-- 29 dashboard 2 -->
<section class="slide c5 r5">
  <div class="ttl" style="top:18px">Dashboard</div>
  <div class="card" style="left:18px;top:48px;width:254px;height:76px"><div class="h abs" style="left:6px;top:4px;font-size:3.4px">Data Statistics</div>
    <svg class="abs" style="left:10px;top:12px" width="240" height="60"><g>
      <rect x="8" y="30" width="6" height="26" fill="#b47d34"/><rect x="26" y="22" width="6" height="34" fill="#d9ad5b"/><rect x="44" y="28" width="6" height="28" fill="#f0d488"/><rect x="62" y="18" width="6" height="38" fill="#3d4863"/><rect x="80" y="14" width="6" height="42" fill="#5865c9"/><rect x="98" y="24" width="6" height="32" fill="#b47d34"/><rect x="116" y="30" width="6" height="26" fill="#d9ad5b"/><rect x="134" y="24" width="6" height="32" fill="#3d4863"/><rect x="152" y="20" width="6" height="36" fill="#c48f3f"/><rect x="170" y="28" width="6" height="28" fill="#f0d488"/><rect x="188" y="14" width="6" height="42" fill="#3d4863"/><rect x="206" y="10" width="6" height="46" fill="#5865c9"/></g></svg></div>
  <div class="card" style="left:280px;top:48px;width:88px;height:76px"><div class="h abs" style="left:6px;top:4px;font-size:3.4px">Customer Email</div>
    <svg class="abs" style="left:22px;top:14px" width="44" height="44"><circle cx="22" cy="22" r="17" fill="none" stroke="#eee" stroke-width="2"/><circle cx="22" cy="22" r="17" fill="none" stroke="#c48f3f" stroke-width="2" stroke-dasharray="80 107" transform="rotate(-90 22 22)"/><circle cx="22" cy="22" r="13" fill="none" stroke="#3d4863" stroke-width="1.5" stroke-dasharray="50 82" transform="rotate(-90 22 22)"/></svg></div>
  <div class="abs" style="left:18px;top:132px;width:350px;display:flex;gap:8px">
    <div class="card" style="position:relative;flex:1;height:42px;padding:4px;text-align:center"><div class="h" style="font-size:3.2px">Sales</div><div style="font-size:3.4px">$7,620</div><div style="height:16px;margin-top:4px;background:linear-gradient(180deg,#f2d1c4,#fff);clip-path:polygon(0 60%,20% 30%,40% 50%,60% 20%,80% 45%,100% 10%,100% 100%,0 100%)"></div></div>
    <div class="card" style="position:relative;flex:1;height:42px;padding:4px;text-align:center"><div class="h" style="font-size:3.2px">Revenue</div><div style="font-size:3.4px">$4,280</div><div style="height:16px;margin-top:4px;background:linear-gradient(180deg,#f6e4b8,#fff);clip-path:polygon(0 40%,20% 55%,40% 25%,60% 45%,80% 20%,100% 35%,100% 100%,0 100%)"></div></div>
    <div class="card" style="position:relative;flex:1;height:42px;padding:4px;text-align:center"><div class="h" style="font-size:3.2px">Clients</div><div style="font-size:3.4px">$5,290</div><div style="height:16px;margin-top:4px;background:linear-gradient(180deg,#c4cfe6,#fff);clip-path:polygon(0 70%,20% 40%,40% 60%,60% 30%,80% 50%,100% 25%,100% 100%,0 100%)"></div></div>
    <div class="card" style="position:relative;flex:1;height:42px;padding:4px;text-align:center"><div class="h" style="font-size:3.2px">Trade</div><div style="font-size:3.4px">$7,780</div><div style="height:16px;margin-top:4px;background:linear-gradient(180deg,#dcc9f0,#fff);clip-path:polygon(0 50%,20% 65%,40% 35%,60% 55%,80% 25%,100% 40%,100% 100%,0 100%)"></div></div>
  </div>
  <div class="foot"><span>nivelcrest.com</span><i class="mk"></i><span>page | 29</span></div>
</section>

<!-- 30 dashboard 3 -->
<section class="slide c6 r5">
  <div class="ttl" style="top:18px">Dashboard</div>
  <div class="h abs" style="left:30px;top:48px;font-size:3.4px;color:var(--gold)">Net Profit Margin</div>
  <svg class="abs" style="left:28px;top:54px" width="230" height="50">
    <polyline points="6,22 38,12 70,30 102,14 134,28 166,12 198,24 226,16" fill="none" stroke="#c48f3f" stroke-width=".8" stroke-dasharray="2 1.5"/>
    <polyline points="6,34 38,28 70,38 102,30 134,40 166,26 198,36 226,30" fill="none" stroke="#3d4863" stroke-width=".8" stroke-dasharray="2 1.5"/>
    <g fill="#c48f3f"><circle cx="38" cy="12" r="1.2"/><circle cx="102" cy="14" r="1.2"/><circle cx="166" cy="12" r="1.2"/><circle cx="226" cy="16" r="1.2"/></g>
  </svg>
  <div class="card" style="left:268px;top:46px;width:100px;height:64px;padding:4px 8px"><div class="h" style="font-size:3.4px;color:var(--gold)">Rate Profitability Indicator</div>
    <div style="font-size:3px;color:#999;margin-top:4px;line-height:12px">Data One<br>Data Two<br>Data Three<br>Data Four</div>
    <div class="bar" style="left:44px;top:14px;width:20px;background:#f0d488"></div><div class="bar" style="left:44px;top:26px;width:16px;background:#3d4863"></div><div class="bar" style="left:44px;top:38px;width:26px;background:#d9ad5b"></div><div class="bar" style="left:44px;top:50px;width:30px;background:#a9b3c8"></div></div>
  <div class="h abs" style="left:28px;top:116px;font-size:3.4px;color:var(--gold)">Past Year vs Target vs Actual</div>
  <svg class="abs" style="left:28px;top:122px" width="230" height="56">
    <g fill="#3d4863"><rect x="8" y="30" width="4" height="20"/><rect x="36" y="26" width="4" height="24"/><rect x="64" y="32" width="4" height="18"/><rect x="92" y="24" width="4" height="26"/><rect x="120" y="28" width="4" height="22"/><rect x="148" y="20" width="4" height="30"/><rect x="176" y="26" width="4" height="24"/><rect x="204" y="22" width="4" height="28"/></g>
    <g fill="#c48f3f"><rect x="14" y="34" width="4" height="16"/><rect x="42" y="30" width="4" height="20"/><rect x="70" y="36" width="4" height="14"/><rect x="98" y="28" width="4" height="22"/><rect x="126" y="32" width="4" height="18"/><rect x="154" y="26" width="4" height="24"/><rect x="182" y="30" width="4" height="20"/><rect x="210" y="26" width="4" height="24"/></g>
    <polyline points="10,28 40,22 70,26 100,18 130,22 160,8 190,20 220,16" fill="none" stroke="#d9ad5b" stroke-width=".8"/>
  </svg>
  <div class="abs" style="left:270px;top:128px;width:96px"><div style="font-size:6px"><span class="gold">●</span> 68,780.930</div><p class="p" style="color:var(--gold);font-size:3.2px">Total planned value across all active builds this year.</p></div>
  <div class="foot"><span>nivelcrest.com</span><i class="mk"></i><span>page | 30</span></div>
</section>

<!-- 31 gantt -->
<section class="slide c1 r6">
  <div class="ttl" style="top:14px">Dashboard</div>
  <svg class="abs" style="left:20px;top:44px" width="350" height="130">
    <g stroke="#eee" stroke-width=".5"><line x1="80" y1="0" x2="80" y2="120"/><line x1="108" y1="0" x2="108" y2="120"/><line x1="136" y1="0" x2="136" y2="120"/><line x1="164" y1="0" x2="164" y2="120"/><line x1="192" y1="0" x2="192" y2="120"/><line x1="220" y1="0" x2="220" y2="120"/><line x1="248" y1="0" x2="248" y2="120"/><line x1="276" y1="0" x2="276" y2="120"/><line x1="304" y1="0" x2="304" y2="120"/><line x1="332" y1="0" x2="332" y2="120"/></g>
    <g font-size="3" fill="#aaa" font-family="Poppins,sans-serif"><text x="74" y="5">May</text><text x="102" y="5">Jun</text><text x="132" y="5">Jul</text><text x="158" y="5">Aug</text><text x="186" y="5">Sep</text><text x="214" y="5">Oct</text><text x="242" y="5">Nov</text><text x="270" y="5">Dec</text><text x="300" y="5">Jan</text></g>
    <g font-size="3.4" fill="#c48f3f" font-family="Poppins,sans-serif"><text x="30" y="30">Team One</text><text x="30" y="66">Team Two</text><text x="30" y="102">Team Three</text></g>
    <rect x="8" y="26" width="14" height="5" rx="2.5" fill="#b47d34"/><rect x="8" y="62" width="14" height="5" rx="2.5" fill="#f0d488"/><rect x="8" y="98" width="14" height="5" rx="2.5" fill="#3d4863"/>
    <rect x="98" y="28" width="44" height="10" rx="5" fill="#b47d34"/><rect x="192" y="28" width="128" height="10" rx="5" fill="#3d4863"/>
    <rect x="150" y="48" width="120" height="10" rx="5" fill="#f0d488"/><rect x="126" y="62" width="56" height="10" rx="5" fill="#3d4863"/><rect x="210" y="62" width="96" height="10" rx="5" fill="#b47d34"/>
    <rect x="116" y="88" width="120" height="10" rx="5" fill="#b47d34"/><rect x="284" y="88" width="48" height="10" rx="5" fill="#f0d488"/>
    <g fill="#c48f3f"><circle cx="84" cy="120" r="1.4"/><circle cx="112" cy="120" r="1.4"/><circle cx="140" cy="120" r="1.4"/><circle cx="168" cy="120" r="1.4"/><circle cx="196" cy="120" r="1.4"/><circle cx="224" cy="120" r="1.4"/><circle cx="252" cy="120" r="1.4"/><circle cx="280" cy="120" r="1.4"/><circle cx="308" cy="120" r="1.4"/><circle cx="336" cy="120" r="1.4"/></g>
    <g font-size="3" fill="#999" font-family="Poppins,sans-serif"><text x="78" y="128">2022</text><text x="106" y="128">2022</text><text x="134" y="128">2022</text><text x="162" y="128">2022</text><text x="190" y="128">2022</text><text x="218" y="128">2022</text><text x="246" y="128">2022</text><text x="274" y="128">2022</text><text x="302" y="128">2022</text><text x="330" y="128">2023</text></g>
  </svg>
  <div class="foot"><span>nivelcrest.com</span><i class="mk"></i><span>page | 31</span></div>
</section>

<!-- 32 thank you -->
<section class="slide dark c2 r6">
  <div class="abs" style="left:0;right:0;top:64px;text-align:center;font-size:22px;font-weight:700;color:var(--gold-lt);background:linear-gradient(90deg,#b47d34,#f0cd72,#b47d34);-webkit-background-clip:text;background-clip:text;color:transparent">Thank You</div>
  <div class="abs" style="left:112px;top:96px;width:162px;height:.8px;background:var(--gold)"></div>
  <p class="abs" style="left:90px;top:106px;width:206px;text-align:center;font-size:3.6px;line-height:5.5px;color:#ddd">Thank you for your time. We look forward to planning your next build together and keeping every cost in view.</p>
  <div class="abs" style="left:0;right:0;top:128px;display:flex;justify-content:center;gap:28px"><i style="width:9px;height:9px;border:.8px solid #fff;border-radius:50%;display:block"></i><i style="width:9px;height:9px;border:.8px solid #fff;border-radius:50%;display:block"></i><i style="width:9px;height:9px;border:.8px solid #fff;border-radius:50%;display:block"></i></div>
</section>

<!-- 33-36 icon sets -->
<section class="slide c3 r6" aria-label="Icon set page one"><div class="icons"></div></section>
<section class="slide c4 r6" aria-label="Icon set page two"><div class="icons"></div></section>
<section class="slide c5 r6" aria-label="Icon set page three"><div class="icons"></div></section>
<section class="slide c6 r6" aria-label="Icon set page four"><div class="icons"></div></section>

</div>
</body>
</html>
```